Printer Cartridges Supplier Namecard

Attached is my company logo and the design of my current namecard. I would like to have a more special look for it. Can have a little cuteness too rather than those normal standard feel. I'm a supplier mainly dealing with original and compatible printer toner cartridges, some other products like paper supplies as well.

Target Market(s)

Companies, businesses, corporates

Industry/Entity Type

It Company

Contact Information for Business Card

Logo, name, contact, address, supplies and maybe a slogan

Colors
85cae6
33a6d7
3176b5
0255a3
0792cd
85abd2

Requirements
Must have
• Logo, name, contact and address basic details.
• Must include some pictures, not just rearrange what I'm currently having.
Nice to have
• Be creative and bold, a diiferent traditional feel.

```html
<!DOCTYPE html>
<html lang="en">
<head>
<meta charset="utf-8">
<title>Tonerbay Namecard</title>
<link href="https://fonts.googleapis.com/css2?family=Lato:wght@400;700&display=swap" rel="stylesheet">
<style>
  :root {
    --stage: #21272e;
    --card-front: #ffffff;
    --card-back: #64b5e4;
    --accent: #1b9ad6;
    --ink: #3c3c3c;
    --ink-soft: #575757;
    --rule: #d5d5d5;
    --shadow: rgba(0, 0, 0, 0.55);
  }
  * { margin: 0; padding: 0; box-sizing: border-box; }
  html, body { width: 1200px; height: 900px; overflow: hidden; }
  body {
    background: var(--stage);
    font-family: "Lato", Arial, sans-serif;
    position: relative;
  }
  .card {
    position: absolute;
    top: 306px;
    width: 439px;
    height: 271px;
    border-radius: 12px;
    box-shadow: 3px 4px 4px var(--shadow);
  }
  .card--front { left: 149px; background: var(--card-front); }
  .card--back { left: 609px; background: var(--card-back); }

  .brand-name {
    position: absolute;
    font-weight: 400;
    color: var(--ink-soft);
    letter-spacing: 0.5px;
    line-height: 1;
  }
  .card--front .brand-name { left: 30px; top: 112px; font-size: 46px; }

  .divider {
    position: absolute;
    left: 225px; top: 72px;
    width: 1px; height: 149px;
    background: var(--rule);
  }
  .contact {
    position: absolute;
    left: 240px; top: 67px;
    color: var(--ink);
    font-size: 12.5px;
    line-height: 15.5px;
  }
  .contact__name { color: var(--accent); font-size: 18px; font-weight: 700; line-height: 22px; }
  .contact__role { margin-bottom: 12px; }
  .contact__address { margin-bottom: 10px; }
  .contact__line { display: flex; align-items: center; gap: 4px; }
  .contact__line svg { width: 9px; height: 9px; flex: none; }

  .card--back .brand-mark {
    position: absolute;
    left: 82px; top: 44px;
    width: 62px; height: 62px;
    background: #ffffff;
    border-radius: 8px;
  }
  .card--back .brand-name { left: 158px; top: 44px; font-size: 56px; }
  .tagline {
    position: absolute;
    left: 176px; top: 100px;
    font-size: 9px;
    color: var(--ink-soft);
  }
  .supplies {
    position: absolute;
    left: 135px; top: 140px;
    list-style: none;
    color: var(--ink);
    font-size: 12.5px;
    font-weight: 700;
  }
  .supplies li { display: flex; align-items: center; gap: 5px; height: 23px; }
  .supplies svg { width: 10px; height: 9px; }
</style>
</head>
<body>
  <section class="card card--front">
    <div class="brand-name">tonerbay</div>
    <div class="divider"></div>
    <div class="contact">
      <div class="contact__name">Mira Tanley</div>
      <div class="contact__role">Sales Executive</div>
      <div class="contact__address">
        14A Harbourlight Avenue<br>#05-112<br>Singapore 530417
      </div>
      <div class="contact__line">
        <svg viewBox="0 0 10 10"><rect x="2.5" y="0.5" width="5" height="9" rx="1" fill="none" stroke="var(--accent)" stroke-width="1.3"/></svg>
        9100 4826
      </div>
      <div class="contact__line">
        <svg viewBox="0 0 10 10"><rect x="0.5" y="2" width="9" height="6.5" fill="var(--accent)"/><path d="M0.5 2 L5 5.5 L9.5 2" fill="none" stroke="#fff" stroke-width="0.9"/></svg>
        mira@tonerbay.sg
      </div>
      <div class="contact__line">
        <svg viewBox="0 0 10 10"><circle cx="5" cy="5" r="4.5" fill="var(--accent)"/><path d="M2 4 Q4 3 5 5 T8 6" fill="none" stroke="#fff" stroke-width="0.9"/></svg>
        www.tonerbay.sg
      </div>
    </div>
  </section>

  <section class="card card--back">
    <div class="brand-mark"></div>
    <div class="brand-name">tonerbay</div>
    <div class="tagline">Compatible printer ink and toner solutions</div>
    <ul class="supplies">
      <li><svg viewBox="0 0 10 9"><path d="M0 0 L10 4.5 L0 9 L2.5 4.5 Z" fill="var(--ink-soft)"/></svg>Printer Ink &amp; Toner Catridge</li>
      <li><svg viewBox="0 0 10 9"><path d="M0 0 L10 4.5 L0 9 L2.5 4.5 Z" fill="var(--ink-soft)"/></svg>Orginal Printer Catridge</li>
      <li><svg viewBox="0 0 10 9"><path d="M0 0 L10 4.5 L0 9 L2.5 4.5 Z" fill="var(--ink-soft)"/></svg>Paper Product</li>
      <li><svg viewBox="0 0 10 9"><path d="M0 0 L10 4.5 L0 9 L2.5 4.5 Z" fill="var(--ink-soft)"/></svg>Printer Maintance &amp; Repair</li>
    </ul>
  </section>
</body>
</html>
```